Business card for Luxury Portable Restroom Trailer company

We are a Luxury Portable Restroom Trailer Company Called FALCRIDGE HIRES. Based in Orange County California. We provide portable restroom trailers for events, such as, Weddings, Concerts, Charity events, Sporting events, Tournaments, Corporate events, ect. We rent and Sell the Luxury restrooms. Our colors are white, grey, and Orange. As you will see in the logo we uploaded.
There are 2 people in the company so the names and titles will change for the 3 people but card will remain the same. Here is the information for each Person: Dwight Penner CFO 555 318-0476
next Person: Leon Marchetti VP 555 318-0476
Next Person: Owen Marchetti CEO 555 318-0476
Information to include on the card: Luxury Restroom Trailers Rental and Sales. Weddings, Concerts, Charity, Sporting and Corp. Events.

```html
<!DOCTYPE html>
<html lang="en">
<head>
<meta charset="utf-8">
<title>Falcridge Hires – Business Card</title>
<link rel="stylesheet" href="https://fonts.googleapis.com/css2?family=Montserrat:wght@400;500;600;700;800&display=swap">
<style>
  :root {
    --orange: #ec6c26;
    --ink: #4a4a4d;
    --ink-soft: #5c5c60;
    --paper: #ffffff;
    --card-back: #4f4f52;
    --card-back-mark: #47474a;
    --stage: #2a2a2c;
    --rule: #6a6a6e;
  }
  * { box-sizing: border-box; margin: 0; padding: 0; }
  html, body {
    width: 1200px; height: 878px; overflow: hidden;
    background: var(--stage);
    font-family: "Montserrat", sans-serif;
  }
  .stage {
    width: 1200px; height: 878px;
    display: flex; flex-direction: column; align-items: center; justify-content: center;
    gap: 30px;
  }
  .card {
    position: relative; width: 700px; height: 400px; overflow: hidden;
    box-shadow: 0 10px 30px rgba(0,0,0,.45);
  }

  /* Front */
  .card-front { background: var(--paper); color: var(--ink); }
  .mark-ring { position: absolute; left: 0; top: 0; width: 700px; height: 400px; pointer-events: none; }
  .brand {
    position: absolute; left: 48px; top: 42px;
    display: flex; align-items: center; gap: 12px;
  }
  .brand-square { width: 22px; height: 22px; background: var(--orange); }
  .brand-name {
    font-size: 30px; font-weight: 800; letter-spacing: 1px; color: var(--orange);
  }
  .person { position: absolute; left: 48px; top: 128px; }
  .person-name { font-size: 28px; font-weight: 700; letter-spacing: 1px; text-transform: uppercase; color: var(--ink); }
  .person-title { font-size: 16px; font-weight: 400; letter-spacing: 1px; color: var(--ink-soft); margin-top: 2px; }
  .contacts { position: absolute; left: 48px; top: 204px; list-style: none; }
  .contacts li {
    display: flex; align-items: center; gap: 10px;
    font-size: 16px; letter-spacing: .5px; color: var(--ink); margin-bottom: 9px;
  }
  .contacts svg { width: 14px; height: 14px; fill: var(--orange); flex: none; }
  .divider {
    position: absolute; left: 48px; top: 310px; width: 390px; height: 1px; background: var(--rule);
  }
  .tagline {
    position: absolute; left: 48px; top: 322px;
    font-size: 15px; font-weight: 600; color: var(--orange); letter-spacing: .3px;
  }
  .events {
    position: absolute; left: 48px; top: 349px;
    font-size: 15px; font-weight: 400; color: var(--ink-soft); letter-spacing: .4px;
  }

  /* Back */
  .card-back { background: var(--card-back); }
  .back-pattern {
    position: absolute; inset: 0;
    background: radial-gradient(ellipse at 50% 50%, var(--card-back) 0%, var(--card-back-mark) 100%);
  }
  .back-mark { position: absolute; right: 150px; top: 130px; width: 50px; height: 50px; }
</style>
</head>
<body>
<main class="stage">

  <section class="card card-front" aria-label="Business card front">
    <svg class="mark-ring" viewBox="0 0 700 400" aria-hidden="true">
      <circle cx="678" cy="212" r="190" fill="none" stroke="var(--orange)" stroke-width="18"/>
    </svg>

    <div class="brand">
      <span class="brand-square"></span>
      <span class="brand-name">FALCRIDGE HIRES</span>
    </div>

    <div class="person">
      <h1 class="person-name">Owen Marchetti</h1>
      <p class="person-title">CEO</p>
    </div>

    <ul class="contacts">
      <li>
        <svg viewBox="0 0 24 24"><path d="M6.6 10.8a15.1 15.1 0 0 0 6.6 6.6l2.2-2.2c.3-.3.7-.4 1-.2 1.1.4 2.3.6 3.6.6.6 0 1 .4 1 1V20c0 .6-.4 1-1 1A17 17 0 0 1 3 4c0-.6.4-1 1-1h3.5c.6 0 1 .4 1 1 0 1.3.2 2.5.6 3.6.1.3 0 .7-.2 1z"/></svg>
        555 318-0476
      </li>
      <li>
        <svg viewBox="0 0 24 24"><path d="M2 5h20v14H2zm2 2v.5l8 5 8-5V7l-8 5z"/></svg>
        owen@falcridgehires.com
      </li>
      <li>
        <svg viewBox="0 0 24 24"><path d="M12 2a10 10 0 1 0 0 20 10 10 0 0 0 0-20zm6.9 6h-3a15.7 15.7 0 0 0-1.3-3.9A8 8 0 0 1 18.9 8zM12 4c.8 1.2 1.5 2.5 1.9 4h-3.8c.4-1.5 1.1-2.8 1.9-4zM4.3 14a8 8 0 0 1 0-4h3.4a16 16 0 0 0 0 4zm.8 2h3a15.7 15.7 0 0 0 1.3 3.9A8 8 0 0 1 5.1 16zm3-8h-3a8 8 0 0 1 4.3-3.9C8.8 5.3 8.4 6.6 8.1 8zM12 20c-.8-1.2-1.5-2.5-1.9-4h3.8c-.4 1.5-1.1 2.8-1.9 4zm2.3-6H9.7a14.6 14.6 0 0 1 0-4h4.6a14.6 14.6 0 0 1 0 4zm.3 5.9c.6-1.2 1-2.5 1.3-3.9h3a8 8 0 0 1-4.3 3.9zm1.7-5.9a16 16 0 0 0 0-4h3.4a8 8 0 0 1 0 4z"/></svg>
        www.falcridgehires.com
      </li>
    </ul>

    <div class="divider"></div>
    <p class="tagline">Luxury Restroom Trailers Rental and Sales</p>
    <p class="events">Weddings | Concerts | Charity | Sporting | Corp</p>
  </section>

  <section class="card card-back" aria-label="Business card back">
    <div class="back-pattern" role="img" aria-label="Repeating faint embossed brand-mark pattern in dark grey"></div>
    <svg class="back-mark" viewBox="0 0 50 50" aria-hidden="true">
      <circle cx="25" cy="25" r="22" fill="none" stroke="var(--orange)" stroke-width="3"/>
    </svg>
  </section>

</main>
</body>
</html>
```